The Linen Loft Co

We need a business card design for our wardrobe company.
Please visit our website www.gentlelinenlofts.com to get an idea of who we are.

```html
<!DOCTYPE html>
<html lang="en">
<head>
<meta charset="utf-8">
<title>The Linen Loft Co — Business Card</title>
<link href="https://fonts.googleapis.com/css2?family=Roboto:wght@400;500;700&display=swap" rel="stylesheet">
<style>
  :root {
    --backdrop: #e6e4e0;
    --card-black: #0b0b0b;
    --card-white: #ffffff;
    --ink: #111111;
    --ink-soft: #3c3c3c;
    --ink-muted: #a5a5a5;
  }
  html, body {
    margin: 0;
    padding: 0;
    width: 1200px;
    height: 801px;
    overflow: hidden;
    background: var(--backdrop);
    font-family: "Roboto", Arial, sans-serif;
  }
  .business-card {
    position: absolute;
    left: 100px;
    top: 110px;
    width: 1000px;
    height: 580px;
    background: var(--card-black);
    box-shadow: 0 12px 30px rgba(0,0,0,0.18);
    overflow: hidden;
  }
  .card-face {
    position: absolute;
    inset: 0;
    width: 100%;
    height: 100%;
  }
  .card-face path { fill: var(--card-white); }
  .card-content {
    position: absolute;
    inset: 0;
    text-align: center;
    color: var(--ink);
  }
  .brand {
    position: absolute;
    top: 78px;
    left: 0;
    right: 0;
    display: flex;
    justify-content: center;
    align-items: center;
    gap: 18px;
  }
  .brand-square {
    width: 74px;
    height: 74px;
    background: var(--ink);
  }
  .brand-text { text-align: left; }
  .brand-name {
    font-size: 24px;
    font-weight: 500;
    letter-spacing: 0.5px;
    text-transform: uppercase;
    margin: 0;
  }
  .brand-tagline {
    font-size: 20px;
    font-weight: 500;
    margin: 6px 0 0;
  }
  .person-name {
    position: absolute;
    top: 208px;
    left: 0; right: 0;
    margin: 0;
    font-size: 40px;
    font-weight: 700;
  }
  .person-title {
    position: absolute;
    top: 258px;
    left: 0; right: 0;
    margin: 0;
    font-size: 24px;
    font-weight: 500;
    color: var(--ink-muted);
  }
  .contact {
    position: absolute;
    top: 310px;
    left: 0; right: 0;
    font-size: 23px;
    line-height: 38px;
    color: var(--ink-soft);
  }
  .contact p { margin: 0; }
  .contact .label { font-weight: 700; color: var(--ink); }
</style>
</head>
<body>
  <div class="business-card">
    <svg class="card-face" viewBox="0 0 1000 580" preserveAspectRatio="none" aria-hidden="true">
      <path d="M0 0 H940 Q960 250 1000 470 L1000 580 H790 Q330 500 0 390 Z"/>
    </svg>
    <div class="card-content">
      <div class="brand">
        <div class="brand-square"></div>
        <div class="brand-text">
          <p class="brand-name">The Linen Loft Co</p>
          <p class="brand-tagline">Crafted for Every Room</p>
        </div>
      </div>
      <h1 class="person-name">Daniel Harper</h1>
      <p class="person-title">President</p>
      <div class="contact">
        <p>Marlow Court, 48 Elm Street, London N1 4QT</p>
        <p><span class="label">P:</span> 020 7946 0815 <span class="label">E:</span> info@gentlelinenlofts.com</p>
        <p><span class="label">W:</span> www.gentlelinenlofts.com</p>
      </div>
    </div>
  </div>
</body>
</html>
```